Veltrane Group Business Card Design

The CEO is looking for a new trendy look for his business card.
You can stay with current branding or come up with something new/creative. It can be 3D, including Medical Office buildings. You can use our logo in a variety of colors. Please include name, title, company name, company website, email address, cell number

Target Market(s)

Real Estate Development and Construction

Industry/Entity Type

Health care real estate

Contact Information for Business Card

Rohesh Kamdar, CEO M-604.781.2249 E-roheshkamdar@veltrane.com Address:4180 Lindqvist Ave, Tampa, FL 33482 www.veltrane.com

Font styles to use
Other font styles liked:
• Be creative

Requirements
Must have
• Creative, trendy look
Nice to have
• Please go to our website to get a feel- www. veltrane.com
Should not have
• small fonts

```html
<!DOCTYPE html>
<html lang="en">
<head>
<meta charset="utf-8">
<title>Veltrane Group – Business Card</title>
<link rel="stylesheet" href="https://fonts.googleapis.com/css2?family=Roboto:wght@400;700;900&display=swap">
<style>
  :root {
    --brand-red: #b01f2b;
    --brand-red-soft: #e0506a;
    --brand-navy: #1c2a4d;
    --card-white: #ffffff;
    --backdrop: #2b2b2d;
    --text-light: #ffffff;
  }
  * { box-sizing: border-box; margin: 0; padding: 0; }
  html, body {
    width: 1200px; height: 874px; overflow: hidden;
    background: var(--backdrop);
    font-family: "Roboto", Arial, sans-serif;
  }
  .stage {
    width: 1200px; height: 874px;
    display: flex; flex-direction: column;
    align-items: center; justify-content: center; gap: 40px;
  }
  .card {
    position: relative;
    width: 620px; height: 356px;
    border-radius: 22px;
    overflow: hidden;
  }
  /* Front side */
  .card--front { background: var(--brand-red); }
  .front-brand {
    position: absolute; left: 0; right: 0; top: 118px;
    text-align: center;
    color: var(--brand-red-soft);
    font-weight: 900; font-size: 68px; letter-spacing: -1px;
    line-height: 1;
  }
  .front-web {
    position: absolute; left: 0; right: 0; bottom: 42px;
    text-align: center;
    color: var(--text-light);
    font-size: 15px; letter-spacing: 4px;
  }
  /* Back side */
  .card--back { background: var(--card-white); }
  .back-brand {
    position: absolute; left: 36px; top: 40px;
    color: var(--brand-red);
    font-weight: 900; font-size: 44px; letter-spacing: -1px; line-height: 1;
  }
  .back-swoosh { position: absolute; inset: 0; }
  .contact {
    position: absolute; right: 34px; top: 186px;
    text-align: right; color: var(--text-light);
    font-size: 15px; line-height: 1.25;
  }
  .contact__name { font-size: 24px; font-weight: 700; line-height: 1.1; }
  .contact__title { margin-bottom: 6px; }
  .contact__address { margin-bottom: 8px; }
  .contact__line { display: flex; justify-content: flex-end; align-items: center; gap: 8px; }
  .contact__line svg { width: 14px; height: 14px; flex: none; }
</style>
</head>
<body>
<main class="stage">
  <section class="card card--front" aria-label="Card front">
    <div class="front-brand">Veltrane Group</div>
    <div class="front-web">www.veltrane.com</div>
  </section>

  <section class="card card--back" aria-label="Card back">
    <div class="back-brand">Veltrane Group</div>
    <svg class="back-swoosh" viewBox="0 0 620 356" width="620" height="356" aria-hidden="true">
      <path d="M222,356 C252,178 370,132 620,130" fill="none" stroke="var(--brand-navy)" stroke-width="5"/>
      <path d="M240,356 C270,190 380,150 620,146 L620,356 Z" fill="var(--brand-red)"/>
    </svg>
    <div class="contact">
      <div class="contact__name">Rohesh Kamdar</div>
      <div class="contact__title">CEO</div>
      <div class="contact__address">4180 Lindqvist Ave, Tampa<br>FL 33482</div>
      <div class="contact__line">604.781.2249
        <svg viewBox="0 0 24 24"><path fill="#fff" d="M6.6 10.8a15 15 0 0 0 6.6 6.6l2.2-2.2a1 1 0 0 1 1-.25 11.4 11.4 0 0 0 3.6.57 1 1 0 0 1 1 1V20a1 1 0 0 1-1 1A17 17 0 0 1 3 4a1 1 0 0 1 1-1h3.5a1 1 0 0 1 1 1c0 1.25.2 2.45.57 3.57a1 1 0 0 1-.25 1z"/></svg>
      </div>
      <div class="contact__line">roheshkamdar@veltrane.com
        <svg viewBox="0 0 24 24"><path fill="#fff" d="M3 5h18v14H3z M3 5l9 7 9-7" stroke="#b01f2b" stroke-width="1.5"/></svg>
      </div>
      <div class="contact__line">www.veltrane.com
        <svg viewBox="0 0 24 24"><circle cx="12" cy="12" r="10" fill="#fff"/></svg>
      </div>
    </div>
  </section>
</main>
</body>
</html>
```